Financial Services Flyer in English one side Spanish the other side

Hello - we are looking for good flyer that will be one side English, the other side exact same language in Spanish.... For the Flyer -

We show businesses how to save Thousands by Eliminating the percentage you are paying to accept Credit & Debit Cards... No more %!?? Yes, it's true!

We provide a free placed terminal or POS with a minimal monthly service fee.

On the Spanish Side; include "We specialize in Latina Businesses with Spanish Sales and Support staff"
We specialize in Latina Businesses with Spanish Sales and Support staff.
Nos especializamos en negocios latinos con personal de ventas y soporte en espaƱol.

Target Market(s)

Any business

Industry/Entity Type

any business that accepts credit cards.

Requirements
Must have
• WE need a white box on the flyers to place a label with the various agents name and contact.
Nice to have
• You can include pictures I uploaded, especially the logo and some equipment...

```html
<!DOCTYPE html>
<html lang="en">
<head>
<meta charset="utf-8">
<title>Lumora Payments Flyer</title>
<link href="https://fonts.googleapis.com/css2?family=Poppins:wght@500;600;700;800&display=swap" rel="stylesheet">
<style>
  :root {
    --backdrop: #9c9c9c;
    --paper: #eef0f4;
    --white: #ffffff;
    --brand-blue: #1565b3;
    --band-blue: #1b70ba;
    --deep-blue: #155c9f;
    --accent-yellow: #f0c419;
  }
  * { margin: 0; padding: 0; box-sizing: border-box; }
  html, body {
    width: 1200px; height: 872px; overflow: hidden;
    background: var(--backdrop);
    font-family: "Poppins", sans-serif;
  }
  .sheet {
    position: absolute; top: 53px; width: 540px; height: 766px;
    overflow: hidden; background: var(--paper);
    box-shadow: 0 2px 10px rgba(0,0,0,.15);
  }
  .sheet--english { left: 43px; }
  .sheet--spanish { left: 617px; background: var(--white); }
  .waves { position: absolute; inset: 0; width: 540px; height: 766px; }
  .photo { position: absolute; }
  .photo--shopper {
    left: 269px; top: 26px; width: 271px; height: 430px;
    background: linear-gradient(160deg, #e3b98e 0%, #b86d2c 45%, #8a4a1c 100%);
    border-radius: 120px 120px 0 0;
  }
  .photo--counter-terminal {
    left: 160px; top: 344px; width: 150px; height: 243px;
    background: linear-gradient(145deg, #3a3d42 0%, #23262a 60%, #2a6fc0 100%);
    border-radius: 26px;
    transform: rotate(-30deg);
    transform-origin: center;
  }
  .photo--handheld-terminal {
    left: 110px; top: 156px; width: 130px; height: 290px;
    background: linear-gradient(160deg, #2b2d31 0%, #1c1d20 50%, #3a3d42 100%);
    border-radius: 24px;
    transform: rotate(-18deg);
  }
  .photo--keypad-terminal {
    left: 307px; top: 135px; width: 127px; height: 301px;
    background: linear-gradient(180deg, #3b3f46 0%, #4d5560 50%, #2e3238 100%);
    border-radius: 14px;
  }
  .brand-name {
    position: absolute; left: 80px; top: 26px;
    font-size: 42px; font-weight: 700; line-height: 1;
    color: var(--brand-blue); letter-spacing: -1px;
  }
  .headline {
    position: absolute; left: 29px; top: 100px;
    font-size: 25px; font-weight: 800; line-height: 32px;
    color: var(--brand-blue);
  }
  .headline span { display: block; }
  .hl { color: var(--accent-yellow); font-style: normal; }
  .pitch {
    position: absolute; left: 0; width: 540px; text-align: center;
    color: var(--white);
  }
  .pitch--savings { top: 600px; font-size: 13.6px; font-weight: 500; line-height: 19.5px; }
  .pitch--savings .hl { font-weight: 700; }
  .pitch--offer { top: 676px; font-size: 17px; font-weight: 700; line-height: 26px; }
  .es-headline {
    position: absolute; top: 18px; left: 0; width: 540px; text-align: center;
    font-size: 24px; font-weight: 800; line-height: 30px; color: var(--brand-blue);
  }
  .label-grid {
    position: absolute; left: 22px; top: 468px;
    display: grid; grid-template-columns: repeat(3, 158px);
    grid-auto-rows: 89px; column-gap: 11px; row-gap: 13px;
  }
  .label-slot { background: var(--white); border-radius: 3px; }
  .es-cta {
    position: absolute; top: 688px; left: 0; width: 540px; text-align: center;
    font-size: 25px; font-weight: 800; line-height: 30px; color: var(--white);
  }
</style>
</head>
<body>

<section class="sheet sheet--english">
  <div class="photo photo--shopper" role="img" aria-label="Photo of a smiling shopper holding payment cards and shopping bags"></div>
  <svg class="waves" viewBox="0 0 540 766" aria-hidden="true">
    <defs>
      <linearGradient id="blueFieldEn" x1="0" y1="0" x2="0" y2="1">
        <stop offset="0" stop-color="var(--band-blue)"/>
        <stop offset="1" stop-color="var(--deep-blue)"/>
      </linearGradient>
    </defs>
    <path d="M0,340 C120,418 270,452 540,435 L540,766 L0,766 Z" fill="var(--white)"/>
    <path d="M0,352 C130,432 280,472 540,458 L540,766 L0,766 Z" fill="var(--accent-yellow)"/>
    <path d="M0,360 C140,462 300,516 540,505 L540,766 L0,766 Z" fill="url(#blueFieldEn)"/>
  </svg>
  <div class="photo photo--counter-terminal" role="img" aria-label="Photo of a countertop card terminal with a card inserted"></div>

  <div class="brand-name">lumora</div>

  <h1 class="headline">
    <span>LUMORA PAYMENTS</span>
    <span>TAKE THE PAIN OUT</span>
    <span>OF <em class="hl">PAYMENT</em></span>
    <span class="hl">PROCESSING BY</span>
    <span><em class="hl">DELIVERING</em> MORE</span>
    <span>OF YOUR PROFIT</span>
    <span>TO YOU!</span>
  </h1>

  <p class="pitch pitch--savings">
    We show businesses how to save Thousands by Eliminating the<br>
    percentage you are paying to accept Credit &amp; Debit Cards...<br>
    <span class="hl">Pay ZERO % with Lumora!</span>
  </p>
  <p class="pitch pitch--offer">
    We provide a free placed terminal or <span class="hl">POS with a</span><br>
    <span class="hl">minimal monthly service fee.</span>
  </p>
</section>

<section class="sheet sheet--spanish">
  <svg class="waves" viewBox="0 0 540 766" aria-hidden="true">
    <defs>
      <linearGradient id="blueFieldEs" x1="0" y1="0" x2="0" y2="1">
        <stop offset="0" stop-color="var(--band-blue)"/>
        <stop offset="1" stop-color="var(--deep-blue)"/>
      </linearGradient>
    </defs>
    <path d="M0,313 C180,402 360,402 540,314 L540,766 L0,766 Z" fill="var(--accent-yellow)"/>
    <path d="M0,324 C180,414 360,414 540,326 L540,766 L0,766 Z" fill="url(#blueFieldEs)"/>
  </svg>

  <h2 class="es-headline">
    NOS ESPECIALIZAMOS EN NEGOCIOS<br>
    <span class="hl">LATINOS CON PERSONAL DE VENTAS Y</span><br>
    SOPORTE EN ESPAÑOL.
  </h2>

  <div class="photo photo--handheld-terminal" role="img" aria-label="Photo of a handheld touchscreen payment terminal showing a completed sale"></div>
  <div class="photo photo--keypad-terminal" role="img" aria-label="Photo of a keypad payment terminal with contactless reader"></div>

  <div class="label-grid" aria-label="Spaces for agent name and contact labels">
    <div class="label-slot"></div>
    <div class="label-slot"></div>
    <div class="label-slot"></div>
    <div class="label-slot"></div>
    <div class="label-slot"></div>
    <div class="label-slot"></div>
  </div>

  <p class="es-cta">
    CONTACTE CON NUESTRO SOCIO HOY<br>
    <span class="hl">Y ACTIVE SUS AHORROS.</span>
  </p>
</section>

</body>
</html>
```